design a construction company business card

Design business card around our logo. Card must have all the typical info: name, title, address, phone, email, business name, etc. Somewhere on the card I would like to see our motto "Built on integrity... Inspired by commitment." Consider adding a splash of bright orange to the card to complement the blues and silvers/grays in the logo. We are open to metallic inks, textures, etc. We would like to see options on both light and dark backgrounds. The font in the logo is Euro Technic Extended Regular.

```html
<!DOCTYPE html>
<html lang="en">
<head>
<meta charset="utf-8">
<title>Halvern Contracting business cards</title>
<link rel="stylesheet" href="https://fonts.googleapis.com/css2?family=Montserrat:wght@400;500;600&family=Oswald:wght@600&display=swap">
<style>
  :root {
    --page-bg: #1b1b1c;
    --card-bg: #262729;
    --card-edge: #2f3033;
    --brand-blue: #2f7fd6;
    --silver: #b9bcc1;
    --text-light: #e4e5e7;
    --text-muted: #a9abaf;
    --divider: #8a8c90;
  }
  * { margin: 0; padding: 0; box-sizing: border-box; }
  html, body { width: 1200px; height: 960px; overflow: hidden; }
  body {
    background: var(--page-bg);
    font-family: "Montserrat", Arial, sans-serif;
    position: relative;
  }
  .card {
    position: absolute;
    top: 337px;
    width: 500px;
    height: 286px;
    background: linear-gradient(160deg, var(--card-edge) 0%, var(--card-bg) 55%, #222325 100%);
    border-radius: 4px;
    box-shadow: 0 18px 40px rgba(0,0,0,.55);
  }
  .card--front { left: 70px; }
  .card--back { left: 630px; }

  .wordmark {
    position: absolute;
    left: 0; right: 0;
    display: flex;
    flex-direction: column;
    align-items: center;
    gap: 4px;
  }
  .wordmark__name {
    font-family: "Montserrat", Arial, sans-serif;
    font-weight: 600;
    font-size: 34px;
    letter-spacing: 5px;
    line-height: 1;
    display: flex;
    align-items: center;
    gap: 10px;
  }
  .wordmark__square { width: 14px; height: 14px; display: inline-block; }
  .wordmark__sub {
    font-size: 11px;
    letter-spacing: 2px;
    font-weight: 600;
  }
  .card--front .wordmark { top: 52px; }
  .card--front .wordmark__name,
  .card--front .wordmark__sub { color: var(--brand-blue); }
  .card--front .wordmark__square { background: var(--brand-blue); }

  .card--back .wordmark { top: 92px; }
  .card--back .wordmark__name,
  .card--back .wordmark__sub { color: var(--silver); }
  .card--back .wordmark__square { background: var(--silver); }

  .identity {
    position: absolute;
    top: 150px;
    right: 268px;
    text-align: right;
  }
  .identity__name {
    font-family: "Oswald", Arial, sans-serif;
    font-weight: 600;
    font-size: 19px;
    letter-spacing: 1.5px;
    color: var(--brand-blue);
    line-height: 1.1;
  }
  .identity__title {
    font-size: 13px;
    color: var(--text-light);
    margin-top: 2px;
  }
  .divider {
    position: absolute;
    left: 248px;
    top: 146px;
    width: 1px;
    height: 50px;
    background: var(--divider);
  }
  .contact {
    position: absolute;
    left: 262px;
    top: 148px;
    list-style: none;
  }
  .contact__item {
    display: flex;
    align-items: center;
    gap: 9px;
    font-size: 12.5px;
    color: var(--text-light);
    line-height: 16px;
  }
  .contact__icon { width: 11px; height: 11px; fill: var(--brand-blue); flex: none; }
  .address {
    position: absolute;
    left: 0; right: 0;
    top: 222px;
    text-align: center;
    font-size: 12.5px;
    color: var(--text-light);
  }
  .motto {
    position: absolute;
    left: 0; right: 0;
    top: 200px;
    text-align: center;
    font-size: 12px;
    color: var(--text-muted);
    letter-spacing: .3px;
  }
</style>
</head>
<body>
  <section class="card card--front" aria-label="Business card front">
    <div class="wordmark">
      <span class="wordmark__name"><span class="wordmark__square"></span>HALVERN</span>
      <span class="wordmark__sub">CONTRACTING, INC.</span>
    </div>
    <div class="identity">
      <p class="identity__name">YOUR NAME</p>
      <p class="identity__title">Your Title</p>
    </div>
    <div class="divider"></div>
    <ul class="contact">
      <li class="contact__item">
        <svg class="contact__icon" viewBox="0 0 24 24"><path d="M6.6 10.8a15.1 15.1 0 0 0 6.6 6.6l2.2-2.2a1 1 0 0 1 1-.25 11.4 11.4 0 0 0 3.6.57 1 1 0 0 1 1 1V20a1 1 0 0 1-1 1A17 17 0 0 1 3 4a1 1 0 0 1 1-1h3.5a1 1 0 0 1 1 1c0 1.25.2 2.45.57 3.57a1 1 0 0 1-.25 1z"/></svg>
        123-456-2100
      </li>
      <li class="contact__item">
        <svg class="contact__icon" viewBox="0 0 24 24"><path d="M2 5h20v14H2z M3 6l9 7 9-7" fill="none" stroke="#2f7fd6" stroke-width="2.5"/></svg>
        youremail@mailbox.com
      </li>
      <li class="contact__item">
        <svg class="contact__icon" viewBox="0 0 24 24"><circle cx="12" cy="12" r="10" fill="none" stroke="#2f7fd6" stroke-width="2.5"/><path d="M2 12h20M12 2c3 3 3 17 0 20M12 2c-3 3-3 17 0 20" fill="none" stroke="#2f7fd6" stroke-width="2"/></svg>
        www.yourwebsite.com
      </li>
    </ul>
    <p class="address">Your address, city, state, ZIP 0000</p>
  </section>

  <section class="card card--back" aria-label="Business card back">
    <div class="wordmark">
      <span class="wordmark__name"><span class="wordmark__square"></span>HALVERN</span>
      <span class="wordmark__sub">CONTRACTING, INC.</span>
    </div>
    <p class="motto">Built on integrity... Inspired by commitment.</p>
  </section>
</body>
</html>
```